Business card for law firm

Need business card for new law firm. Think confident, authoritative, conservative, but not stuffy or old-fashioned.

Contact Information for Business Card

Content for card - logo (uploaded), plus the following:

Paul Whitcombe (larger font)
Managing Partner (larger font, but not as large as name)
Level 9, 7 Ferris Lane
Sydney NSW 2000
Main Tel 02 9364 2710
Direct Tel 02 8472 3159
Email paul@qvlegal.com.au
www.qvlegal.com.au

Letterhead design should include logo plus:
Level 9, 7 Ferris Lane
Sydney NSW 2000
Tel 02 8472 3159
www.qvlegal.com.au

```html
<!DOCTYPE html>
<html lang="en">
<head>
<meta charset="utf-8">
<title>Quayvale Legal – Business Card</title>
<link rel="stylesheet" href="https://fonts.googleapis.com/css2?family=Cormorant+Garamond:wght@500;600&family=Roboto:wght@300;400&display=swap">
<style>
  :root {
    --navy: #14296b;
    --ink: #1b1b1f;
    --grey: #55565c;
    --paper: #ffffff;
    --backdrop: #e9e6e1;
  }
  * { margin: 0; padding: 0; box-sizing: border-box; }
  html, body { width: 1200px; height: 768px; overflow: hidden; }
  body {
    background: var(--backdrop);
    display: flex;
    align-items: center;
    justify-content: center;
    gap: 40px;
  }
  .card {
    position: relative;
    width: 540px;
    height: 330px;
    background: var(--paper);
    box-shadow: 0 10px 28px rgba(0,0,0,.18);
  }

  /* front */
  .card-front .edge-tab {
    position: absolute;
    left: 0; top: 150px;
    width: 12px; height: 34px;
    background: var(--navy);
  }
  .contact-block { position: absolute; left: 40px; top: 146px; }
  .person-name {
    font-family: "Cormorant Garamond", serif;
    font-weight: 500;
    font-size: 24px;
    letter-spacing: .02em;
    text-transform: uppercase;
    color: var(--navy);
    line-height: 1;
  }
  .person-role {
    font-family: "Cormorant Garamond", serif;
    font-weight: 600;
    font-size: 13px;
    letter-spacing: .04em;
    text-transform: uppercase;
    color: var(--ink);
    margin-top: 3px;
  }
  .address {
    font-family: "Roboto", sans-serif;
    font-weight: 300;
    font-size: 12px;
    color: var(--grey);
    line-height: 1.4;
    margin-top: 16px;
  }
  .details { list-style: none; margin-top: 6px; }
  .details li {
    display: flex; align-items: center; gap: 8px;
    font-family: "Roboto", sans-serif;
    font-weight: 300;
    font-size: 12px;
    color: var(--grey);
    line-height: 1.45;
  }
  .details svg { width: 10px; height: 10px; fill: var(--navy); flex: none; }

  .wordmark { font-family: "Cormorant Garamond", serif; color: var(--ink); text-align: center; }
  .wordmark .firm { font-weight: 500; text-transform: uppercase; line-height: 1; }
  .wordmark .kind { font-weight: 500; text-transform: uppercase; color: var(--grey); }

  .card-front .wordmark { position: absolute; right: 40px; bottom: 36px; }
  .card-front .firm { font-size: 40px; letter-spacing: .02em; }
  .card-front .kind { font-size: 12px; letter-spacing: 1.05em; margin-top: 4px; margin-right: -1.05em; }

  /* back */
  .card-back { display: flex; align-items: center; justify-content: center; }
  .back-mark { display: flex; align-items: center; gap: 18px; }
  .back-mark .square { width: 30px; height: 30px; background: var(--navy); }
  .card-back .firm { font-size: 38px; letter-spacing: .02em; }
  .card-back .kind { font-size: 11px; letter-spacing: 1.05em; margin-top: 4px; margin-right: -1.05em; }
</style>
</head>
<body>

<section class="card card-front" aria-label="Card front">
  <div class="edge-tab"></div>
  <div class="contact-block">
    <p class="person-name">Paul Whitcombe</p>
    <p class="person-role">Managing Partner</p>
    <p class="address">Level 9, 7 Ferris Lane<br>Sydney NSW 2000</p>
    <ul class="details">
      <li><svg viewBox="0 0 10 10"><path d="M2 0.5 L4 2.5 L3 3.8 Q4.5 6 6.2 7 L7.5 6 L9.5 8 L8 9.5 Q3 9 0.5 2 Z"/></svg>02 9364 2710</li>
      <li><svg viewBox="0 0 10 10"><path d="M2 0.5 L4 2.5 L3 3.8 Q4.5 6 6.2 7 L7.5 6 L9.5 8 L8 9.5 Q3 9 0.5 2 Z"/></svg>02 8472 3159</li>
      <li><svg viewBox="0 0 10 10"><path d="M0 2 H10 V8.5 H0 Z M0.8 2.6 L5 5.6 L9.2 2.6" stroke="#fff" stroke-width=".8"/></svg>paul@qvlegal.com.au</li>
      <li><svg viewBox="0 0 10 10"><circle cx="5" cy="5" r="4.8"/><path d="M0.5 5 H9.5 M5 0.5 Q2 5 5 9.5 M5 0.5 Q8 5 5 9.5" stroke="#fff" stroke-width=".6" fill="none"/></svg>www.qvlegal.com.au</li>
    </ul>
  </div>
  <div class="wordmark">
    <p class="firm">Quayvale</p>
    <p class="kind">Legal</p>
  </div>
</section>

<section class="card card-back" aria-label="Card back">
  <div class="back-mark">
    <div class="wordmark">
      <p class="firm">Quayvale</p>
      <p class="kind">Legal</p>
    </div>
    <div class="square"></div>
  </div>
</section>

</body>
</html>
```